New Fun, Positive, energised looking Business Card Needed for High Achiever Coach

I am looking for a two sided full colour business card. I am self employed and have recently re branded my 1-2-1 work re-vitalising high achievers. My target client base for these cards is therefore high achievers - usually aged 40 -55, they are often entrepreneurs, CEO or work in banking and finance and 2/3 are male. I work with them on 90 day or 6 month coaching programs to help them live their success in a healthier, more sustainable and fulfiiled way. They pay for this privately so though they are corporate types the cards need not look 'corporate'. I want to portray the idea of transformation, vitality and re-connecting.
You can get a feel for the look I like on my new website: morvenlisk.co.uk
I want to use this logo with strapline (Re-Vitalising High Achievers) (I purchased off Logoharbor) and font/ colours (the turquoise and green).
Details to include on the card:
www.morvenlisk.co.uk
+44 7915 302618
morven@morvenlisk.co.uk
skype: morvenlisk
I'd also like to include:
Do you struggle to switch off? Want to be healthier and feel fitter? Want closer relationships? More clarity over the direction you are headed? I can help you do these things using integrated mind-body techniques. Visit morvenlisk.co.uk TODAY to apply for a FREE Breakthrough session.
BUT if that is too much text for a card I am open to advice/ammendments.
Updates
Thanks for your design - I am considering them. PLease change the wording to :

```html
<!DOCTYPE html>
<html lang="en">
<head>
<meta charset="utf-8">
<title>Morven Lisk – Business Card</title>
<link href="https://fonts.googleapis.com/css2?family=Open+Sans:wght@400;600;700&display=swap" rel="stylesheet">
<style>
  :root {
    --turquoise: #1aa3c8;
    --green: #5cb85c;
    --ink: #3a3a3a;
    --rule: #b9bcc0;
    --card: #ffffff;
    --backdrop: #eceef2;
  }
  * { box-sizing: border-box; margin: 0; padding: 0; }
  html, body {
    width: 1200px; height: 987px; overflow: hidden;
    background: var(--backdrop);
    font-family: "Open Sans", Arial, sans-serif;
    color: var(--ink);
  }
  .card {
    position: absolute; left: 230px;
    width: 740px; height: 436px;
    background: var(--card);
    border-radius: 36px;
    box-shadow: 0 6px 18px rgba(0,0,0,0.12);
    overflow: hidden;
  }
  .card--front { top: 40px; }
  .card--back { top: 510px; }

  .brand { display: flex; align-items: center; gap: 16px; }
  .brand__dot { width: 48px; height: 48px; border-radius: 50%; background: var(--green); flex: none; }
  .brand__name { font-size: 46px; font-weight: 700; color: var(--turquoise); line-height: 1; }

  .card--front .brand { position: absolute; left: 60px; top: 110px; }
  .front__rule {
    position: absolute; left: 0; right: 0; top: 270px; height: 2px;
    background: linear-gradient(90deg, rgba(185,188,192,0.2), var(--rule) 35%, #8f9296);
  }
  .contacts { position: absolute; left: 44px; top: 298px; list-style: none; }
  .contacts li { display: flex; align-items: center; gap: 10px; font-size: 20px; line-height: 32px; }
  .contacts svg { width: 18px; height: 18px; flex: none; }
  .contacts .icon-square { width: 16px; height: 16px; border-radius: 3px; background: var(--turquoise); flex: none; }
  .website {
    position: absolute; right: 46px; bottom: 46px;
    font-size: 30px; letter-spacing: 2.5px; color: var(--ink);
  }
  .website span { color: var(--turquoise); }

  .card--back .brand { position: absolute; left: 34px; top: 190px; }
  .card--back .brand__name { font-size: 36px; }
  .card--back .brand__dot { width: 38px; height: 38px; }
  .back__rule {
    position: absolute; left: 316px; top: 40px; bottom: 60px; width: 1.5px;
    background: linear-gradient(180deg, #8f9296, rgba(185,188,192,0.2));
  }
  .pitch { position: absolute; left: 338px; top: 44px; width: 380px; font-size: 17px; line-height: 25px; }
  .pitch p + p { margin-top: 8px; }
  .pitch strong { font-weight: 700; }
</style>
</head>
<body>
  <section class="card card--front" aria-label="Card front">
    <div class="brand">
      <span class="brand__dot" aria-hidden="true"></span>
      <span class="brand__name">Morven Lisk</span>
    </div>
    <div class="front__rule"></div>
    <ul class="contacts">
      <li>
        <svg viewBox="0 0 20 20" aria-hidden="true"><circle cx="10" cy="10" r="9" fill="none" stroke="#1aa3c8" stroke-width="1.6"/><path d="M7 5.5l2 2-1 1.2c.6 1.3 1.5 2.2 2.8 2.8l1.2-1 2 2-1.3 1.5c-3.5-.3-6.7-3.5-7-7z" fill="#1aa3c8"/></svg>
        +44 7915 302618
      </li>
      <li>
        <svg viewBox="0 0 20 20" aria-hidden="true"><rect x="2" y="5" width="16" height="11" rx="2" fill="#1aa3c8"/><path d="M2.5 6l7.5 5.5L17.5 6" fill="none" stroke="#fff" stroke-width="1.4"/></svg>
        morven@morvenlisk.co.uk
      </li>
      <li>
        <span class="icon-square" aria-hidden="true"></span>
        morvenlisk
      </li>
    </ul>
    <div class="website">www.<span>morvenlisk</span>.co.uk</div>
  </section>

  <section class="card card--back" aria-label="Card back">
    <div class="brand">
      <span class="brand__dot" aria-hidden="true"></span>
      <span class="brand__name">Morven Lisk</span>
    </div>
    <div class="back__rule"></div>
    <div class="pitch">
      <p>Do you struggle to switch off?<br>
      Want to be healthier and feel fitter?<br>
      Want closer relationships?<br>
      More clarity over the direction you are headed?</p>
      <p>I can help you do these things using integrated mind-body techniques.</p>
      <p>Visit <strong>morvenlisk.co.uk</strong> TODAY to apply for a FREE Breakthrough session.</p>
    </div>
  </section>
</body>
</html>
```